Elegant Business Card for Technology Company

Client is a supplier of innovative industrial communications and automation equipment since 2002. This contest is to gather fresh ideas for a redesign of the existing business card. Client is looking for design that best communicates tagline "Industrial Networking and Computing Specialist".

Design submissions should look modern, clean, elegant and professional. It should not be cluttered. Use white as the primary colour. Orange and black as secondary colour. Refer to jpeg File 1 on the current design.

Fonts used by Client used include Arial Regular, Arial Black, Roboto Regular, Roboto Black and Lato.

The winning design will be sent for offset printing using super white 250gsm artcard paper (open for suggestions).

Target Market(s)

System Engineers, Project Managers, Purchasing Managers from companies providing engineering services for Smart Cities.

Industry/Entity Type

Information Technology

Contact Information for Business Card

Refer to PDF File 3 for Business Card Details. Priority of short contact information would be as follows Name > Job Title > Email > Mobile > Web > Tel > Fax > Business Address >UEN (UEN represents company registration number)

Font styles to use
Sans Serif

Colors
ffffff
f37122
000000
5c5c5c

Requirements
Must have
• Refer to AI File 2 (Company Logo) & PDF File 3 (Information on Namecard)
Should not have
• No QR codes
• No Social Media Icons
• Do not create full Black or Orange colour background

```html
<!DOCTYPE html>
<html lang="en">
<head>
<meta charset="utf-8">
<title>KVR Business Card</title>
<link href="https://fonts.googleapis.com/css2?family=Open+Sans:wght@400;600;800&display=swap" rel="stylesheet">
<style>
  :root {
    --orange: #f37122;
    --white: #ffffff;
    --black: #000000;
    --grey: #5c5c5c;
    --backdrop: #e9e6e1;
  }
  * { box-sizing: border-box; margin: 0; padding: 0; }
  html, body { width: 1200px; height: 950px; overflow: hidden; }
  body {
    background: var(--backdrop);
    font-family: "Open Sans", Arial, sans-serif;
    display: flex;
    flex-direction: column;
    align-items: center;
    justify-content: center;
    gap: 30px;
  }
  .card {
    position: relative;
    width: 760px;
    height: 434px;
    border-radius: 22px;
    overflow: hidden;
    background: var(--white);
    box-shadow: 0 6px 20px rgba(0,0,0,.16);
  }

  .brand {
    display: flex;
    align-items: center;
    gap: 14px;
    font-weight: 800;
    letter-spacing: 2px;
    line-height: 1;
  }
  .brand-dot { border-radius: 50%; flex: none; background: var(--orange); }

  /* Card back: white with tagline */
  .card-back {
    display: flex;
    flex-direction: column;
    align-items: center;
    justify-content: center;
    text-align: center;
  }
  .card-back .brand { font-size: 84px; color: var(--orange); margin-bottom: 30px; }
  .card-back .brand-dot { width: 60px; height: 60px; }
  .tagline { font-size: 16px; line-height: 1.5; color: var(--grey); }
  .tagline strong { color: var(--black); font-weight: 600; }

  /* Card front: white with contact details */
  .card-front .wave { position: absolute; inset: 0; }
  .card-front .brand {
    position: absolute;
    top: 56px;
    left: 350px;
    font-size: 76px;
    color: var(--black);
  }
  .card-front .brand-dot { width: 62px; height: 62px; }
  .person {
    position: absolute;
    right: 46px;
    top: 222px;
    text-align: right;
  }
  .person-name { color: var(--orange); font-size: 21px; font-weight: 600; line-height: 1.2; }
  .person-title { color: var(--black); font-size: 15px; }
  .contact {
    position: absolute;
    left: 52px;
    top: 236px;
    color: var(--white);
    font-size: 15px;
    line-height: 19px;
  }
  .address { margin-bottom: 12px; }
  .contact-list { list-style: none; }
  .contact-list li { display: flex; align-items: center; gap: 10px; height: 20px; }
  .contact-list svg { width: 14px; height: 14px; flex: none; }
</style>
</head>
<body>

  <section class="card card-back">
    <div class="brand"><span class="brand-dot"></span>KVR</div>
    <p class="tagline">
      <strong>Industrial Networking &amp; Computing Specialist</strong><br>
      Industrial Ethernet / Wireless / Cellular<br>
      Industrial &amp; Embedded Computing / Serial / Fieldbus Connectivity<br>
      IP Video Surveillance / Remote Automation
    </p>
  </section>

  <section class="card card-front">
    <svg class="wave" viewBox="0 0 760 434" aria-hidden="true">
      <path d="M0,205 C170,130 470,130 600,434 L0,434 Z" fill="var(--orange)"/>
      <path d="M40,190 C200,118 520,118 640,434 L600,434 C470,130 170,130 0,205 Z" fill="var(--black)"/>
    </svg>

    <div class="brand"><span class="brand-dot"></span>KVR</div>

    <div class="person">
      <p class="person-name">Daniel Lim</p>
      <p class="person-title">Sales Manager</p>
    </div>

    <div class="contact">
      <p class="address">22 Kallang Way Tech Hub<br>#05-12 (Lobby B)<br>Singapore 349201</p>
      <ul class="contact-list">
        <li>
          <svg viewBox="0 0 14 14"><path d="M3 1 L5.5 1 L6.5 4 L5 5.2 Q6.3 8 8.8 9 L10 7.5 L13 8.5 L13 11 Q12 13 10 13 Q1 11 1 3 Q1 1 3 1 Z" fill="var(--white)"/></svg>
          +65 6123 4501
        </li>
        <li>
          <svg viewBox="0 0 14 14"><rect x="3.5" y="0.5" width="7" height="13" rx="1.2" fill="none" stroke="var(--white)" stroke-width="1.4"/><circle cx="7" cy="11" r="0.9" fill="var(--white)"/></svg>
          +65 9123 4567
        </li>
        <li>
          <svg viewBox="0 0 14 14"><rect x="1" y="5" width="12" height="7" rx="1" fill="var(--white)"/><rect x="3.5" y="1" width="7" height="4" fill="none" stroke="var(--white)" stroke-width="1.3"/></svg>
          +65 6123 4599
        </li>
        <li>
          <svg viewBox="0 0 14 14"><rect x="1" y="3" width="12" height="8.5" rx="1" fill="var(--white)"/><path d="M1.5 3.5 L7 8 L12.5 3.5" fill="none" stroke="var(--orange)" stroke-width="1.2"/></svg>
          sales@kvr.com.sg
        </li>
        <li>
          <svg viewBox="0 0 14 14"><circle cx="7" cy="7" r="6" fill="none" stroke="var(--white)" stroke-width="1.3"/><ellipse cx="7" cy="7" rx="2.5" ry="6" fill="none" stroke="var(--white)" stroke-width="1"/><path d="M1 7 H13" stroke="var(--white)" stroke-width="1"/></svg>
          www.kvr.com.sg
        </li>
      </ul>
    </div>
  </section>

</body>
</html>
```